Ridgeline Orchards Organic Cherry POS card 7x11

We are wanting to create a one-sided 7 x 11 organic cherry card that is eye catching and informative.This should be clear and easy to read and not cluttered. We use these cards as a display in grocery stores, demo stands, and other events to market Organic Ridgeline Sweet Orchards. We have a few facts that we would like displayed on the card (see attachment).

Target Market(s)

Consumers

Industry/Entity Type

Agriculture

Requirements
Must have
• Natural color palettes
• Easy to read
• Ridgeline Orchards
Nice to have
• Unique, realistic cherry design

```html
<!DOCTYPE html>
<html lang="en">
<head>
<meta charset="utf-8">
<title>Ridgeline Orchards – Organic Cherry Card</title>
<link href="https://fonts.googleapis.com/css2?family=Great+Vibes&family=Source+Sans+3:wght@400;600&display=swap" rel="stylesheet">
<style>
  :root {
    --paper: #ffffff;
    --paper-shade: #ecebe9;
    --ink: #4a3b35;
    --list-ink: #3f3a38;
    --cherry: #c0172a;
    --cherry-dark: #8e0f1c;
    --leaf: #5bb23a;
    --leaf-dark: #2f8a2b;
    --tick: #3fb24a;
    --photo-light: #f1eeec;
    --photo-mid: #d9cfcc;
    --photo-fruit: #a3202c;
  }
  * { margin: 0; padding: 0; box-sizing: border-box; }
  html, body { width: 1200px; height: 836px; overflow: hidden; background: #f4f4f4; }
  .card {
    position: relative;
    width: 1200px; height: 836px;
    background: linear-gradient(180deg, var(--paper) 0%, var(--paper-shade) 100%);
    overflow: hidden;
    font-family: "Source Sans 3", sans-serif;
  }
  .hero-photo {
    position: absolute; left: 0; top: 200px; width: 720px; height: 636px;
    background:
      radial-gradient(ellipse 38% 30% at 46% 30%, var(--photo-fruit) 0%, rgba(163,32,44,0.75) 55%, rgba(163,32,44,0) 100%),
      radial-gradient(ellipse 60% 55% at 45% 45%, var(--photo-mid) 0%, var(--photo-light) 70%, rgba(241,238,236,0) 100%);
  }
  .brand {
    position: absolute; left: 52px; top: 86px;
    display: flex; align-items: center; gap: 18px;
  }
  .brand-dot { width: 64px; height: 64px; border-radius: 50%; background: var(--cherry-dark); }
  .brand-name { font-size: 56px; font-weight: 600; color: #1f1a1a; letter-spacing: 0.5px; }
  .headline {
    position: absolute; left: 660px; top: 68px; width: 530px;
    font-family: "Great Vibes", cursive; font-size: 44px; line-height: 50px;
    color: var(--ink); text-align: center;
  }
  .ribbon {
    position: absolute; left: 663px; top: 216px; width: 537px; height: 106px;
    background: linear-gradient(90deg, var(--cherry) 0%, #b5142a 60%, var(--cherry-dark) 100%);
    box-shadow: 0 4px 6px rgba(0,0,0,0.25);
    color: #fff; font-size: 52px; font-weight: 400;
    display: flex; align-items: center; padding-left: 62px; letter-spacing: 0.5px;
  }
  .ribbon-fold { position: absolute; left: 663px; top: 198px; }
  .benefits { position: absolute; left: 726px; top: 358px; list-style: none; }
  .benefits li {
    display: flex; align-items: center; gap: 20px;
    font-size: 31px; color: var(--list-ink); height: 55px;
  }
  .basket-photo {
    position: absolute; left: 1068px; top: 548px; width: 116px; height: 170px;
    border-radius: 40% 40% 20% 20%;
    background: radial-gradient(ellipse 70% 30% at 50% 35%, #b3222e 0%, #c99d63 70%, #d7b888 100%);
  }
  .wave { position: absolute; left: 0; top: 0; }
  .seal {
    position: absolute; left: 20px; top: 598px; width: 120px; height: 120px;
    border-radius: 50%; background: var(--leaf-dark); opacity: 0.85;
  }
  .footer-note {
    position: absolute; left: 700px; top: 748px; width: 480px;
    font-family: "Great Vibes", cursive; font-size: 34px; line-height: 40px;
    color: #fff; text-align: center;
  }
</style>
</head>
<body>
<main class="card">
  <div class="hero-photo" role="img" aria-label="Photo of fresh red cherries in a white colander on a light wooden table"></div>

  <div class="brand">
    <span class="brand-dot"></span>
    <span class="brand-name">Ridgeline Orchards</span>
  </div>

  <p class="headline">Organic Ridgeline cherries make up<br>1/3 of the nation’s production.</p>

  <svg class="ribbon-fold" width="10" height="20" viewBox="0 0 10 20" aria-hidden="true">
    <polygon points="0,20 10,0 10,20" fill="#6d0a15"/>
  </svg>
  <h2 class="ribbon">HEALTH BENEFITS</h2>

  <ul class="benefits">
    <li><svg width="26" height="26" viewBox="0 0 26 26" aria-hidden="true"><circle cx="13" cy="13" r="13" fill="var(--tick)"/><path d="M7 13.5l4 4 8-8" stroke="#fff" stroke-width="2.6" fill="none" stroke-linecap="round" stroke-linejoin="round"/></svg>Fat Free</li>
    <li><svg width="26" height="26" viewBox="0 0 26 26" aria-hidden="true"><circle cx="13" cy="13" r="13" fill="var(--tick)"/><path d="M7 13.5l4 4 8-8" stroke="#fff" stroke-width="2.6" fill="none" stroke-linecap="round" stroke-linejoin="round"/></svg>Source of Vitamin C</li>
    <li><svg width="26" height="26" viewBox="0 0 26 26" aria-hidden="true"><circle cx="13" cy="13" r="13" fill="var(--tick)"/><path d="M7 13.5l4 4 8-8" stroke="#fff" stroke-width="2.6" fill="none" stroke-linecap="round" stroke-linejoin="round"/></svg>A Natural Anti-Inflammatory</li>
    <li><svg width="26" height="26" viewBox="0 0 26 26" aria-hidden="true"><circle cx="13" cy="13" r="13" fill="var(--tick)"/><path d="M7 13.5l4 4 8-8" stroke="#fff" stroke-width="2.6" fill="none" stroke-linecap="round" stroke-linejoin="round"/></svg>Source of Potassium</li>
    <li><svg width="26" height="26" viewBox="0 0 26 26" aria-hidden="true"><circle cx="13" cy="13" r="13" fill="var(--tick)"/><path d="M7 13.5l4 4 8-8" stroke="#fff" stroke-width="2.6" fill="none" stroke-linecap="round" stroke-linejoin="round"/></svg>Source of Melatonin</li>
  </ul>

  <svg class="wave" width="1200" height="836" viewBox="0 0 1200 836" aria-hidden="true">
    <defs>
      <linearGradient id="bandRed" x1="0" x2="1" y1="0" y2="0">
        <stop offset="0" stop-color="#c8192b"/>
        <stop offset="0.6" stop-color="#a8121f"/>
        <stop offset="1" stop-color="#8a0d1a"/>
      </linearGradient>
      <linearGradient id="bandGreen" x1="0" x2="1">
        <stop offset="0" stop-color="#2f8a2b"/>
        <stop offset="1" stop-color="#7cc242"/>
      </linearGradient>
    </defs>
    <path d="M0,754 C250,780 480,770 690,700 C850,648 1020,640 1200,676 L1200,700 C1020,666 860,676 700,724 C500,784 260,790 0,762 Z" fill="url(#bandGreen)"/>
    <path d="M0,770 C260,800 500,792 710,730 C880,680 1040,672 1200,704 L1200,836 L0,836 Z" fill="#ffffff"/>
    <path d="M0,780 C260,808 500,802 720,742 C890,694 1050,688 1200,716 L1200,836 L0,836 Z" fill="url(#bandRed)"/>
  </svg>

  <div class="basket-photo" role="img" aria-label="Photo of a wicker basket filled with cherries"></div>
  <div class="seal" role="img" aria-label="Organic certification seal"></div>

  <p class="footer-note">Washington State is the nation’s largest<br>producer of organic cherries.</p>
</main>
</body>
</html>
```